Canadian Christian Church needs design for new sermon series

A graphic design for our series and an invitation card to invite people to the series. Check design brief for more detailed information. Target audience: young families and young adults. Looking for a creative design that will get people's attention and create interest. See design brief for copy of design purchased for previous series.
Updates
entered Apr 4 incorrectly. Need a week to receive and review designs, and today is Apr 2/19. Thanks!
Target Market(s)
young families and young adults
Colors
Designer to choose colors to be used in the design.
Look and feel

```html
<!DOCTYPE html>
<html lang="en">
<head>
<meta charset="utf-8">
<title>Messy – Sermon Series Invitation Card</title>
<link href="https://fonts.googleapis.com/css2?family=Anton&family=Roboto+Slab:wght@400;700&family=Montserrat:wght@400;600;700&family=Lato:wght@400&display=swap" rel="stylesheet">
<style>
  :root{
    --page:#e6e6e6;
    --card:#c8bda2;
    --card-light:#dcd3bd;
    --band:#3d322d;
    --ink:#2f2a26;
    --orange:#f28a12;
    --orange-light:#ffb43a;
    --purple:#7d2a8c;
    --blue:#1f6fc0;
    --white:#ffffff;
  }
  *{box-sizing:border-box;margin:0;padding:0}
  html,body{width:1200px;height:903px;overflow:hidden;background:var(--page)}
  body{position:relative;font-family:'Montserrat',sans-serif;color:var(--ink)}

  .card{position:absolute;width:483px;height:379px;overflow:hidden;
    background:radial-gradient(ellipse 80% 60% at 85% 40%,var(--card-light) 0%,var(--card) 60%);
    box-shadow:0 2px 6px rgba(0,0,0,.25)}
  .card--front{left:177px;top:60px}
  .card--back{left:582px;top:469px}

  /* front */
  .church-name{position:absolute;left:38px;top:70px;display:flex;align-items:center;gap:6px;
    font-family:'Roboto Slab',serif;font-size:12px;color:var(--ink)}
  .church-name .dot{width:12px;height:12px;border-radius:50%;background:var(--orange)}
  .series-title{position:absolute;right:34px;top:22px;font-family:'Anton',sans-serif;font-size:72px;line-height:1;
    letter-spacing:1px;background:linear-gradient(180deg,var(--orange-light),var(--orange) 70%);
    -webkit-background-clip:text;background-clip:text;color:transparent;
    -webkit-text-stroke:1.5px var(--purple)}
  .photo{position:absolute;left:0;top:117px;width:483px;height:221px;
    background:linear-gradient(160deg,#6b6158 0%,#2c2623 45%,#4a4039 75%,#8a7e70 100%)}
  .tagline{position:absolute;left:0;right:0;top:288px;text-align:center;font-family:'Roboto Slab',serif;
    font-size:34px;color:var(--orange);-webkit-text-stroke:1px #3a2208;line-height:1}
  .band{position:absolute;left:0;right:0;bottom:0;background:var(--band);color:var(--white)}
  .card--front .band{height:41px;display:flex;align-items:center;justify-content:center;
    font-family:'Roboto Slab',serif;font-size:21px}

  /* back */
  .services-title{position:absolute;left:0;right:0;top:26px;text-align:center;font-family:'Roboto Slab',serif;
    font-weight:700;font-size:26px;line-height:1.22;color:var(--ink)}
  .services-title .time{font-family:'Montserrat',sans-serif;font-size:26px}
  .info{position:absolute;left:27px;top:104px;font-size:11.4px;line-height:14.6px}
  .info h2{font-size:12.5px;font-weight:600;margin-bottom:1px}
  .info ul{list-style:none;margin-bottom:16px}
  .info li{display:flex;align-items:center;gap:7px}
  .info li::before{content:"";width:7px;height:7px;border-radius:50%;flex:none;
    background:var(--blue);box-shadow:inset 0 0 0 1.5px var(--blue),inset 0 0 0 2.5px #cfe0f4}
  .info b{font-weight:600}
  .values{position:absolute;left:286px;top:108px;width:175px;height:165px}
  .card--back .band{height:57px;font-family:'Lato',sans-serif;font-size:11px;color:var(--white)}
  .contact{position:absolute;left:28px;top:12px;line-height:17px}
  .contact span{display:inline-flex;align-items:center;gap:4px;margin-right:14px}
  .contact svg{width:9px;height:9px}
  .person{position:absolute;left:288px;top:12px;line-height:15px}
  .person .email{color:var(--orange)}
</style>
</head>
<body>

<section class="card card--front">
  <div class="church-name"><span class="dot"></span>Maple Grove Family Church</div>
  <h1 class="series-title">MESSY</h1>
  <div class="photo" role="img" aria-label="Photo of a cluttered desk covered in papers, folders and office items"></div>
  <p class="tagline">Joining God in the Mess</p>
  <div class="band">Connecting Young Families to Christ</div>
</section>

<section class="card card--back">
  <h2 class="services-title">THE TIME OF THE SERVICES:<br><span class="time">Sundays @ 10:30</span></h2>
  <div class="info">
    <h2>Names &amp; Dates of the sermons:</h2>
    <ul>
      <li><span><b>April 28th:</b> “We Made This Mess”</span></li>
      <li><span><b>May 5th:</b> “Bless in the Mess”</span></li>
      <li><span><b>May 12th:</b> “Born into the Mess”</span></li>
      <li><span><b>May 19th:</b> “Messy Work”</span></li>
      <li><span><b>May 26th:</b> “Messy Church”</span></li>
      <li><span><b>June 2nd:</b> “Messy Hospitality”</span></li>
      <li><span><b>June 9th:</b>&nbsp; TBD</span></li>
      <li><span><b>June 16th:</b> “Messy within Boundaries”</span></li>
    </ul>
    <h2>Features of the service:</h2>
    <ul>
      <li>Staffed nursery &amp; children’s program every Sunday</li>
      <li>Coffee &amp; snacks</li>
      <li>Everyone welcome</li>
    </ul>
  </div>
  <div class="values" role="img" aria-label="Core values diagram of interlocking ribbons: Equipping, Serving, Missional Living, Spirit-Living, Belonging"
       style="border-radius:50%;background:radial-gradient(circle,var(--card-light) 22%,var(--orange) 23%,var(--orange) 45%,var(--blue) 46%,var(--blue) 68%,var(--purple) 69%,var(--purple) 72%,transparent 73%)"></div>
  <div class="band">
    <div class="contact">
      <span><svg viewBox="0 0 10 10"><path d="M5 0a3.5 3.5 0 0 0-3.5 3.5C1.5 6 5 10 5 10s3.5-4 3.5-6.5A3.5 3.5 0 0 0 5 0zm0 5a1.4 1.4 0 1 1 0-2.8A1.4 1.4 0 0 1 5 5z" fill="var(--orange)"/></svg>1185 Cedar Ridge Road Oakville, ON L6H 2T4</span><br>
      <span><svg viewBox="0 0 10 10"><path d="M2 .5l2 2-1 1.2a6 6 0 0 0 3.3 3.3l1.2-1 2 2-1.3 1.5C4.5 9.5.5 5.5.5 1.8z" fill="var(--orange)"/></svg>905-555-0148</span><span><svg viewBox="0 0 10 10"><circle cx="5" cy="5" r="4.2" fill="none" stroke="var(--orange)" stroke-width="1"/><path d="M.8 5h8.4M5 .8c-2.5 2.8-2.5 5.6 0 8.4M5 .8c2.5 2.8 2.5 5.6 0 8.4" fill="none" stroke="var(--orange)" stroke-width=".8"/></svg>www.maplegrovechurch.ca</span>
    </div>
    <div class="person">Please contact Laura Bennett<br><span class="email">worship@maplegrovechurch.ca</span></div>
  </div>
</section>

</body>
</html>
```